Thornbury Building Company - Card Design

I am looking to use the logo designs that you already did for me to develop a business card. I would like the card to have a black background and be double sided. I want white and green logo and text. I have attached an inspiration photo of a look that I like. I would like to use the Vertical Logo attached to take up the full front side of the card. On the back where I have my name and information, I would like to have the horizontal logo or maybe even just the image of the 'A' and trees without the text. I am open, but I am looking for something clean and simple and I want the green to really pop! Additional files can be found under Design #: 58302946

Target Market(s)

Homeowners

Industry/Entity Type

Construction

Contact Information for Business Card

Name: Marcus Thornbury, Title: Project Manager, Phone: 555.274.8136, Email: thornburybuildingcompany@mailvesta.com, address: 487 Larkspur Ln, Felton, CA 95033, Lic# 2468317

Colors
00AB8E
00BBA5
67D7C9
C6EFE9
E9F9F6

Requirements
Nice to have
• I would like to see the logos that I have already got from ArtLoomHub, though I am open to new ones

```html
<!DOCTYPE html>
<html lang="en">
<head>
<meta charset="utf-8">
<title>Thornbury Building Company – Business Card</title>
<link rel="stylesheet" href="https://fonts.googleapis.com/css2?family=Poppins:wght@400;600;700&display=swap">
<style>
  :root {
    --page-bg: #8a8a8a;
    --card-bg: #232323;
    --ink-white: #ffffff;
    --ink-green: #3db54a;
    --ink-emboss: #3c3c3c;
  }
  * { margin: 0; padding: 0; box-sizing: border-box; }
  html, body {
    width: 900px; height: 1200px; overflow: hidden;
    background: var(--page-bg);
    font-family: "Poppins", sans-serif;
  }
  .card {
    position: absolute;
    left: 119px;
    width: 662px;
    height: 375px;
    background: var(--card-bg);
  }
  .card--front { top: 203px; }
  .card--back  { top: 620px; }

  .front-name {
    position: absolute;
    left: 0; right: 0; top: 150px;
    text-align: center;
    color: var(--ink-emboss);
    font-weight: 700;
    font-size: 34px;
    letter-spacing: 1px;
    line-height: 1.25;
    text-transform: uppercase;
  }

  .holder { position: absolute; left: 36px; top: 42px; }
  .holder-name {
    color: var(--ink-green);
    font-weight: 700;
    font-size: 25px;
    line-height: 1.1;
  }
  .holder-title {
    color: var(--ink-white);
    font-size: 15px;
    letter-spacing: 0.5px;
    margin-top: 2px;
  }

  .contact {
    position: absolute; left: 36px; top: 200px;
    color: var(--ink-white);
    font-size: 15px;
    letter-spacing: 0.6px;
  }
  .contact-address { line-height: 24px; margin-bottom: 7px; }
  .contact-line {
    display: flex; align-items: center; gap: 6px;
    height: 25px;
  }
  .contact-line--phone { letter-spacing: 2.5px; }
  .contact-line svg { width: 16px; height: 16px; flex: none; fill: var(--ink-green); }
  .contact-license {
    color: var(--ink-green);
    font-weight: 700;
    margin-top: 5px;
    letter-spacing: 0.5px;
  }

  .back-name {
    position: absolute;
    left: 368px; width: 240px; top: 145px;
    text-align: center;
    color: var(--ink-white);
    font-weight: 700;
    font-size: 24px;
    line-height: 1.25;
    text-transform: uppercase;
  }
</style>
</head>
<body>
  <section class="card card--front">
    <p class="front-name">Thornbury<br>Building Company</p>
  </section>

  <section class="card card--back">
    <div class="holder">
      <h1 class="holder-name">Marcus Thornbury</h1>
      <p class="holder-title">Project Manager</p>
    </div>

    <div class="contact">
      <p class="contact-address">487 Larkspur Ln, Felton,<br>CA 95033</p>
      <p class="contact-line contact-line--phone">
        <svg viewBox="0 0 24 24" aria-hidden="true"><path d="M6.6 10.8a15.1 15.1 0 0 0 6.6 6.6l2.2-2.2a1 1 0 0 1 1-.25 11.4 11.4 0 0 0 3.6.57 1 1 0 0 1 1 1V20a1 1 0 0 1-1 1A17 17 0 0 1 3 4a1 1 0 0 1 1-1h3.5a1 1 0 0 1 1 1c0 1.25.2 2.45.57 3.6a1 1 0 0 1-.25 1z"/></svg>
        555.274.8136
      </p>
      <p class="contact-line">
        <svg viewBox="0 0 24 24" aria-hidden="true"><path d="M2 5h20v14H2z M2 5l10 8 10-8" fill="var(--ink-green)"/><path d="M2 6l10 8 10-8" fill="none" stroke="#232323" stroke-width="1.6"/></svg>
        thornburybuildingcompany@mailvesta.com
      </p>
      <p class="contact-license">Lic# 2468317</p>
    </div>

    <p class="back-name">Thornbury<br>Building Company</p>
  </section>
</body>
</html>
```